Corvy

Electronic Repairs for OEM's Industrial electronic repairs, consumer audio visual, Projectors

Target Market(s)

manufacturer of electronics (OEM), business, Government, then Consumer

Industry/Entity Type

Electronic Repair

Contact Information for Business Card

Board Repair, Projectors

Font styles to use
Serif

Colors
0054AA
0677BA
7BADD7
CADEEF
E8F1F8

Requirements
Must have
• projector, led wall image
Nice to have
• professional looking business card.
Should not have
• unsure

```html
<!DOCTYPE html>
<html lang="en">
<head>
<meta charset="utf-8">
<title>Corvy Electronic Repairs – Business Card</title>
<link rel="stylesheet" href="https://fonts.googleapis.com/css2?family=Poppins:wght@300;400;600;700;800&family=Roboto+Condensed:wght@400;700&display=swap">
<style>
  :root {
    --blue-deep: #0054AA;
    --blue-mid: #0677BA;
    --blue-soft: #7BADD7;
    --blue-pale: #CADEEF;
    --card-paper: #E8ECEF;
    --backdrop: #D9DEE3;
    --ink: #151a22;
    --white: #ffffff;
  }
  * { margin: 0; padding: 0; box-sizing: border-box; }
  html, body { width: 1200px; height: 840px; overflow: hidden; }
  body {
    background: var(--backdrop);
    font-family: "Poppins", Arial, sans-serif;
    position: relative;
  }
  .business-card {
    position: absolute;
    left: 100px;
    top: 134px;
    width: 1000px;
    height: 572px;
    border-radius: 34px;
    overflow: hidden;
    background: var(--card-paper);
    box-shadow: 0 14px 40px rgba(20, 40, 70, 0.25);
  }
  .card-art { position: absolute; inset: 0; }
  .brand-name {
    position: absolute;
    left: 82px;
    top: 40px;
    font-size: 132px;
    font-weight: 700;
    letter-spacing: -2px;
    line-height: 1;
    color: var(--blue-deep);
  }
  .brand-subtitle {
    position: absolute;
    left: 88px;
    top: 178px;
    font-size: 37px;
    font-weight: 400;
    letter-spacing: 0.5px;
    line-height: 1;
    color: var(--blue-mid);
  }
  .service-summary {
    position: absolute;
    left: 88px;
    top: 246px;
    width: 560px;
    font-size: 20px;
    font-weight: 600;
    line-height: 1.2;
    color: var(--blue-deep);
  }
  .service-list {
    position: absolute;
    left: 90px;
    top: 340px;
    list-style: none;
  }
  .service-item {
    display: flex;
    align-items: center;
    gap: 14px;
    font-size: 23px;
    font-weight: 400;
    line-height: 32px;
    color: var(--ink);
  }
  .tick-icon { width: 22px; height: 22px; flex: none; }
  .call-line {
    position: absolute;
    left: 88px;
    top: 440px;
    font-size: 36px;
    font-weight: 700;
    line-height: 1;
    color: var(--blue-deep);
  }
  .email-line {
    position: absolute;
    left: 88px;
    top: 484px;
    font-family: "Roboto Condensed", "Arial Narrow", sans-serif;
    font-size: 30px;
    font-weight: 700;
    line-height: 1;
    color: var(--ink);
  }
  .address-line {
    position: absolute;
    left: 88px;
    top: 524px;
    font-family: "Roboto Condensed", "Arial Narrow", sans-serif;
    font-size: 23px;
    font-weight: 400;
    line-height: 1;
    color: var(--ink);
  }
</style>
</head>
<body>
  <div class="business-card">
    <svg class="card-art" width="1000" height="572" viewBox="0 0 1000 572">
      <defs>
        <radialGradient id="projectorTone" cx="50%" cy="55%" r="60%">
          <stop offset="0" stop-color="#9fb8e8"/>
          <stop offset="0.35" stop-color="#1f6a86"/>
          <stop offset="1" stop-color="#0c2d3f"/>
        </radialGradient>
        <radialGradient id="ledWallTone" cx="35%" cy="25%" r="80%">
          <stop offset="0" stop-color="#e0467f"/>
          <stop offset="0.5" stop-color="#5a1e45"/>
          <stop offset="1" stop-color="#0f0f1c"/>
        </radialGradient>
        <linearGradient id="circuitTone" x1="0" y1="0" x2="1" y2="1">
          <stop offset="0" stop-color="#9fb4cc"/>
          <stop offset="0.5" stop-color="#2c5e9a"/>
          <stop offset="1" stop-color="#0d2c5f"/>
        </linearGradient>
      </defs>
      <path class="accent-band" d="M748 0 C 628 150, 628 430, 772 572 L1000 572 L1000 0 Z" fill="var(--blue-mid)"/>
      <path class="main-band" d="M778 0 C 660 150, 660 430, 800 572 L1000 572 L1000 0 Z" fill="var(--blue-deep)"/>

      <circle cx="712" cy="148" r="114" fill="var(--blue-pale)"/>
      <circle cx="712" cy="148" r="108" fill="url(#projectorTone)" role="img" aria-label="Photo of a projector being repaired"/>

      <circle cx="860" cy="262" r="110" fill="var(--blue-pale)"/>
      <circle cx="860" cy="262" r="104" fill="url(#ledWallTone)" role="img" aria-label="Close-up photo of an LED wall panel"/>

      <circle cx="748" cy="378" r="114" fill="var(--blue-pale)"/>
      <circle cx="748" cy="378" r="108" fill="url(#circuitTone)" role="img" aria-label="Close-up photo of a circuit board"/>
    </svg>

    <h1 class="brand-name">CORVY</h1>
    <p class="brand-subtitle">ELECTRONIC REPAIRS</p>
    <p class="service-summary">Electronic Repairs for<br>OEM's Industrial electronic repairs,<br>consumer audio visual, Projectors</p>

    <ul class="service-list">
      <li class="service-item">
        <svg class="tick-icon" viewBox="0 0 22 22"><circle cx="11" cy="11" r="11" fill="var(--blue-deep)"/><path d="M6 11.5l3.2 3.2L16 8" fill="none" stroke="var(--white)" stroke-width="2.6" stroke-linecap="round" stroke-linejoin="round"/></svg>
        Projector
      </li>
      <li class="service-item">
        <svg class="tick-icon" viewBox="0 0 22 22"><circle cx="11" cy="11" r="11" fill="var(--blue-deep)"/><path d="M6 11.5l3.2 3.2L16 8" fill="none" stroke="var(--white)" stroke-width="2.6" stroke-linecap="round" stroke-linejoin="round"/></svg>
        Led wall image
      </li>
      <li class="service-item">
        <svg class="tick-icon" viewBox="0 0 22 22"><circle cx="11" cy="11" r="11" fill="var(--blue-deep)"/><path d="M6 11.5l3.2 3.2L16 8" fill="none" stroke="var(--white)" stroke-width="2.6" stroke-linecap="round" stroke-linejoin="round"/></svg>
        Board Repair
      </li>
    </ul>

    <p class="call-line">CALL US 555-210 4832</p>
    <p class="email-line">info@corvyelectronicrepairs.com</p>
    <p class="address-line">2140 Birchwood Road, Fairview, Oregon 97024</p>
  </div>
</body>
</html>
```